Harbor Crestline (Business Card Design)

Need business cards designed. Something modern, chic, and sleek. Mabye the back of the card should be the navy blue that is in the logo and then just the logo on the back.

Target Market(s)

Those in the hotel, office, and renovation industry

Contact Information for Business Card

1. Logo 2. Dorian Fenwick 3. CEO/Founder 4. Phone: (833) HarbCre / (833) 427-2731 5. Email: dorian@theharborcrestline.com 6. Website: www.theharborcrestline.com

Font styles to use
Other font styles liked:
• Look at the logo font and base the font for everything else off of that.

Colors
0054AA
0677BA
7BADD7
CADEEF
E8F1F8

Requirements
Must have
• Colors that are associated in the logo
Nice to have
• Sleek modern clean and chic design.

```html
<!DOCTYPE html>
<html lang="en">
<head>
<meta charset="UTF-8">
<title>Harbor Crestline – Business Card</title>
<link rel="stylesheet" href="https://fonts.googleapis.com/css2?family=Montserrat:wght@500;600;700&family=Open+Sans:wght@400;600;700&display=swap">
<style>
  :root {
    --navy: #0b1741;
    --navy-deep: #081133;
    --navy-light: #1c2f72;
    --gold: #c99d45;
    --white: #ffffff;
    --rule: rgba(255,255,255,0.45);
    --backdrop: #2a2b2e;
  }
  * { box-sizing: border-box; margin: 0; padding: 0; }
  html, body { width: 1200px; height: 780px; overflow: hidden; }
  body {
    background: var(--backdrop);
    display: flex;
    align-items: center;
    justify-content: center;
    gap: 40px;
    font-family: "Open Sans", Arial, sans-serif;
  }
  .card {
    position: relative;
    width: 540px;
    height: 310px;
    background: var(--navy);
    overflow: hidden;
    border-radius: 4px;
  }

  /* front */
  .brand {
    position: absolute;
    left: 40px;
    top: 92px;
    display: flex;
    align-items: center;
    gap: 12px;
  }
  .brand-mark {
    width: 20px;
    height: 20px;
    background: var(--gold);
  }
  .brand-name {
    font-family: "Montserrat", Arial, sans-serif;
    font-weight: 600;
    font-size: 21px;
    letter-spacing: 2px;
    text-transform: uppercase;
    color: var(--white);
    line-height: 1.15;
  }
  .divider {
    position: absolute;
    left: 250px;
    top: 52px;
    width: 1px;
    height: 150px;
    background: var(--rule);
    transform: rotate(14deg);
  }
  .person {
    position: absolute;
    left: 285px;
    top: 50px;
  }
  .person-name {
    font-family: "Open Sans", Arial, sans-serif;
    font-weight: 700;
    font-size: 29px;
    line-height: 1.1;
    color: var(--white);
  }
  .person-name .first { color: var(--gold); }
  .person-title {
    margin-top: 4px;
    font-size: 14px;
    color: var(--white);
  }
  .contact {
    list-style: none;
    margin-top: 16px;
    display: flex;
    flex-direction: column;
    gap: 5px;
  }
  .contact li {
    display: flex;
    align-items: center;
    gap: 8px;
    font-size: 11.5px;
    color: var(--white);
    white-space: nowrap;
  }
  .contact svg { width: 12px; height: 12px; flex: none; }
  .address-band {
    position: absolute;
    left: 0;
    bottom: 34px;
    width: 430px;
    height: 28px;
    background: var(--gold);
    display: flex;
    align-items: center;
    padding-left: 40px;
    font-size: 13px;
    color: var(--white);
    letter-spacing: 0.2px;
  }
  .corner-mark {
    position: absolute;
    left: 444px;
    bottom: 34px;
    width: 28px;
    height: 28px;
    border: 3px solid var(--white);
  }
  .corner-strip {
    position: absolute;
    right: 0;
    bottom: 34px;
    width: 54px;
    height: 28px;
    background: var(--white);
  }

  /* back */
  .pattern-field {
    position: absolute;
    inset: 0;
    background: linear-gradient(120deg, var(--navy-deep) 0%, var(--navy) 45%, var(--navy-light) 100%);
  }
  .back-brand {
    position: absolute;
    right: 120px;
    bottom: 58px;
    display: flex;
    align-items: center;
    gap: 8px;
  }
  .back-brand .brand-mark { width: 12px; height: 12px; background: var(--white); }
  .back-brand .brand-name { font-size: 13px; letter-spacing: 1.5px; }
</style>
</head>
<body>

  <section class="card card-front" aria-label="Business card front">
    <div class="brand">
      <span class="brand-mark"></span>
      <span class="brand-name">Harbor<br>Crestline</span>
    </div>

    <div class="divider"></div>

    <div class="person">
      <h1 class="person-name"><span class="first">Dorian</span> Fenwick</h1>
      <p class="person-title">CEO/Founder</p>
      <ul class="contact">
        <li>
          <svg viewBox="0 0 24 24" aria-hidden="true"><path fill="#c99d45" d="M6.6 10.8a15.1 15.1 0 0 0 6.6 6.6l2.2-2.2a1 1 0 0 1 1-.25 11.4 11.4 0 0 0 3.6.57 1 1 0 0 1 1 1V20a1 1 0 0 1-1 1A17 17 0 0 1 3 4a1 1 0 0 1 1-1h3.5a1 1 0 0 1 1 1c0 1.25.2 2.45.57 3.6a1 1 0 0 1-.25 1z"/></svg>
          (833) HarbCre / (833) 427-2731
        </li>
        <li>
          <svg viewBox="0 0 24 24" aria-hidden="true"><circle cx="12" cy="12" r="9" fill="none" stroke="#c99d45" stroke-width="2"/><path d="M3 12h18M12 3c3 3 3 15 0 18M12 3c-3 3-3 15 0 18" fill="none" stroke="#c99d45" stroke-width="1.6"/></svg>
          www.theharborcrestline.com
        </li>
        <li>
          <svg viewBox="0 0 24 24" aria-hidden="true"><rect x="2" y="5" width="20" height="14" rx="1.5" fill="#c99d45"/><path d="M3 6l9 7 9-7" fill="none" stroke="#0b1741" stroke-width="1.8"/></svg>
          dorian@theharborcrestline.com
        </li>
      </ul>
    </div>

    <div class="address-band">4120 Lakeview Pkwy Suite 2200, Easton, MD 21601</div>
    <div class="corner-mark"></div>
    <div class="corner-strip"></div>
  </section>

  <section class="card card-back" aria-label="Business card back">
    <div class="pattern-field" role="img" aria-label="Repeating brand pattern in navy tones fading to lighter blue"></div>
    <div class="back-brand">
      <span class="brand-mark"></span>
      <span class="brand-name">Harbor Crestline</span>
    </div>
  </section>

</body>
</html>
```